Pellmore's Pick magazine ad

This is a full page ad in a magazine announcing that I won The Pick Of Pellmore Valley Realtor for 2023. The dimensions for the full page ad are 7.125" x 9.75"
I would like it to say "Thank You Harford County for voting me Pellmore's Pick Realtor for 2022 & 2023!"

I am honored that the residents of this county have recognized my integrity, values, willingness to go above and beyond, to save my clients tons of money and stress, and to constantly pour back into this community.

If you are ever thinking about buying or selling a house, please don't hesitate to reach out, I am available 24/7 by text or phone call to save you money and provide the best top notch service:

Corwin Ashlund
call/text 410-555-0172

Small at the bottom:
www.MarlowCrestHomes.com
2749 W Amberly Ln, Bel Air, MD 21014
833-555-0149

I am attaching my logo, the Pellmore's Pick 2023 logo, my picture, and last years ad (I'm hoping to make this years ad different and better)

```html
<!DOCTYPE html>
<html lang="en">
<head>
<meta charset="utf-8">
<title>Pellmore's Pick Realtor – Full Page Ad Options</title>
<link rel="stylesheet" href="https://fonts.googleapis.com/css2?family=League+Gothic&family=Mr+Dafoe&family=Mulish:wght@400;700;800;900&display=swap">
<style>
  :root{
    --stage:#9b9a9c;
    --paper:#ffffff;
    --headline-blue:#0a69b1;
    --band-navy:#2148a0;
    --band-blue:#1a74c2;
    --script-red:#c01f2e;
    --script-yellow:#f3e21a;
    --ink:#1b1b1b;
    --logo-navy:#1d2b5a;
    --footer-gray:#9a9a9a;
    --base-black:#1d1d1d;
    --badge-dark:#2a2626;
  }
  *{margin:0;padding:0;box-sizing:border-box}
  html,body{width:1200px;height:819px;overflow:hidden;background:var(--stage)}
  .stage{position:relative;width:1200px;height:819px}
  .ad{position:absolute;top:65px;width:503px;height:688px;background:var(--paper);overflow:hidden;font-family:'Mulish',sans-serif;color:var(--ink)}
  .ad--classic{left:66px}
  .ad--panel{left:618px}
  .top-bar{position:absolute;left:0;top:0;width:100%;height:11px;background:linear-gradient(90deg,var(--band-navy),var(--band-blue))}
  .thanks{position:absolute;left:22px;top:30px;font-family:'Mr Dafoe',cursive;font-size:76px;line-height:1;color:var(--script-red);white-space:nowrap;z-index:2}
  .brand{position:absolute;left:350px;top:60px;width:140px;display:flex;align-items:center;justify-content:center;gap:5px}
  .brand-dot{width:9px;height:9px;border-radius:50%;background:var(--logo-navy)}
  .brand-name{font-family:'Mulish',sans-serif;font-weight:800;font-size:12.5px;color:var(--logo-navy);white-space:nowrap}
  .lead{position:absolute;left:30px;top:106px;font-size:24px;line-height:28px;font-weight:400;white-space:nowrap;z-index:1}
  .headline{position:absolute;left:28px;top:132px;font-family:'League Gothic',sans-serif;font-weight:400;font-size:78px;line-height:72px;color:var(--headline-blue);text-transform:uppercase;letter-spacing:2.5px;white-space:nowrap;z-index:3}
  .headline span{display:block}
  .body-strong,.body-plain{position:absolute;left:27px;font-size:10.8px;line-height:13px;white-space:nowrap;z-index:3}
  .body-strong{top:356px;font-weight:800}
  .body-plain{top:447px;font-weight:400}
  .ad--panel .body-strong{top:354px}
  .ad--panel .body-plain{top:444px}
  .portrait{position:absolute;z-index:2;background:linear-gradient(180deg,#e9e9ec 0%,#c9a48e 14%,#b68670 22%,#e6e6ee 30%,#2f3d5c 44%,#263453 100%);border-radius:46% 46% 4px 4px / 16% 16% 4px 4px}
  .ad--classic .portrait{left:250px;top:258px;width:236px;height:320px}
  .ad--panel .portrait{left:236px;top:259px;width:267px;height:420px}
  .badge{position:absolute;z-index:4}
  .ad--classic .badge{left:61px;top:534px;width:98px;height:88px}
  .ad--panel .badge{left:384px;top:576px;width:98px;height:84px}
  .footer-strip{position:absolute;left:0;top:630px;height:49px;background:var(--footer-gray)}
  .ad--classic .footer-strip{width:280px}
  .ad--panel .footer-strip{width:270px}
  .footer-info{position:absolute;top:637px;width:240px;text-align:center;color:#fff;font-size:10.5px;line-height:12px;font-weight:400;white-space:nowrap;z-index:3}
  .ad--classic .footer-info{left:-9px}
  .ad--panel .footer-info{left:12px}
  .base-bar{position:absolute;left:0;top:679px;width:100%;height:9px;background:var(--base-black);z-index:5}
  .contact-band{position:absolute;left:0;top:0;width:503px;height:688px;z-index:3}
  .contact{position:absolute;text-align:center;color:#fff;z-index:4}
  .ad--classic .contact{left:251px;top:580px;width:240px}
  .ad--panel .contact{left:7px;top:534px;width:250px}
  .agent-name{font-family:'Mr Dafoe',cursive;color:var(--script-yellow);font-size:35px;line-height:40px;white-space:nowrap}
  .call-label{font-weight:900;font-size:17px;line-height:18px;margin-top:3px}
  .phone{font-weight:900;font-size:30px;line-height:30px;letter-spacing:0.3px;white-space:nowrap}
  .contact-panel{position:absolute;left:0;top:533px;width:270px;height:97px;background:linear-gradient(90deg,var(--band-navy),#2352a8);z-index:1}
</style>
</head>
<body>
<main class="stage">

  <!-- Option A: angled contact band -->
  <article class="ad ad--classic">
    <div class="top-bar"></div>
    <div class="thanks">Thank you</div>
    <div class="brand"><span class="brand-dot"></span><span class="brand-name">Marlow Crest Team</span></div>
    <p class="lead">Harford County for voting me</p>
    <div class="portrait" role="img" aria-label="Portrait photo of the realtor in a navy suit jacket and light striped shirt"></div>
    <h1 class="headline"><span>Pellmore's Pick</span><span>Realtor for 2022</span><span>&amp; 2023!</span></h1>
    <p class="body-strong">I am honored that the residents of this<br>county have recognized my integrity,<br>values, willingness to go above and<br>beyond, to save my clients tons of money<br>and stress, and to constantly pour back<br>into this community.</p>
    <p class="body-plain">If you are ever thinking about buying or<br>selling a house, please don't hesitate<br>to reach out, I am available 24/7 by<br>text or phone call to save you money<br>and provide the best top notch<br>service:</p>
    <svg class="badge" viewBox="0 0 100 88" aria-hidden="true"><polygon points="25,0 75,0 100,22 100,66 75,88 25,88 0,66 0,22" fill="var(--badge-dark)"/></svg>
    <div class="footer-strip"></div>
    <div class="footer-info">www.MarlowCrestHomes.com<br>2749 W Amberly Ln, Bel Air, MD 21014<br>833-555-0149</div>
    <svg class="contact-band" viewBox="0 0 503 688" aria-hidden="true">
      <defs>
        <linearGradient id="bandFill" x1="0" x2="1" y1="0" y2="0">
          <stop offset="0" stop-color="#2148a0"/><stop offset="1" stop-color="#1a74c2"/>
        </linearGradient>
      </defs>
      <path d="M212,679 L262,596 Q274,578 298,578 L503,578 L503,679 Z" fill="url(#bandFill)"/>
    </svg>
    <div class="contact">
      <div class="agent-name">Corwin Ashlund</div>
      <div class="call-label">call/text</div>
      <div class="phone">410-555-0172</div>
    </div>
    <div class="base-bar"></div>
  </article>

  <!-- Option B: contact panel beside portrait -->
  <article class="ad ad--panel">
    <div class="top-bar"></div>
    <div class="thanks">Thank you</div>
    <div class="brand"><span class="brand-dot"></span><span class="brand-name">Marlow Crest Team</span></div>
    <p class="lead">Harford County for voting me</p>
    <div class="portrait" role="img" aria-label="Portrait photo of the realtor in a navy suit jacket and light striped shirt"></div>
    <h1 class="headline"><span>Pellmore's Pick</span><span>Realtor for 2022</span><span>&amp; 2023!</span></h1>
    <p class="body-strong">I am honored that the residents of this<br>county have recognized my integrity,<br>values, willingness to go above and<br>beyond, to save my clients tons of<br>money and stress, and to constantly<br>pour back into this community.</p>
    <p class="body-plain">If you are ever thinking about buying or<br>selling a house, please don't hesitate<br>to reach out, I am available 24/7 by<br>text or phone call to save you money<br>and provide the best top notch<br>service:</p>
    <div class="contact-panel"></div>
    <div class="footer-strip"></div>
    <div class="footer-info">www.MarlowCrestHomes.com<br>2749 W Amberly Ln, Bel Air, MD 21014<br>833-555-0149</div>
    <div class="contact">
      <div class="agent-name">Corwin Ashlund</div>
      <div class="call-label">call/text</div>
      <div class="phone">410-555-0172</div>
    </div>
    <svg class="badge" viewBox="0 0 100 86" aria-hidden="true"><polygon points="25,0 75,0 100,21 100,65 75,86 25,86 0,65 0,21" fill="var(--badge-dark)"/></svg>
    <div class="base-bar"></div>
  </article>

</main>
</body>
</html>
```